Modern Business Card

Modern professional business card with more than just logo and demographic info. Something memorable.

We are a trendy/modern chiropractic group with an emphasis on neurology, hence the minimalist-type brain logo. We want to convey that modern and technical aspect with professionalism and the elite nature of our practice environment.

```html
<!DOCTYPE html>
<html lang="en">
<head>
<meta charset="utf-8">
<title>Keystone Chiropractic – Business Card</title>
<link href="https://fonts.googleapis.com/css2?family=Cinzel:wght@400;500&family=Montserrat:wght@400;500&display=swap" rel="stylesheet">
<style>
  :root {
    --page: #dedfe0;
    --brand-blue: #4a80c2;
    --ink: #1c1c1c;
    --ink-soft: #3a3a3a;
    --white: #ffffff;
  }
  * { box-sizing: border-box; margin: 0; padding: 0; }
  html, body {
    width: 1200px; height: 930px; overflow: hidden;
    background: var(--page);
  }
  .stage { position: relative; width: 1200px; height: 930px; }

  .card {
    position: absolute;
    width: 525px; height: 300px;
    border-radius: 22px;
    overflow: hidden;
    box-shadow: 0 6px 14px rgba(0,0,0,0.18);
  }

  /* Front */
  .card-front {
    left: 70px; top: 110px;
    background: var(--brand-blue);
    display: flex; align-items: center; justify-content: center;
  }
  .wordmark {
    font-family: "Cinzel", serif;
    font-weight: 400;
    line-height: 0.95;
  }
  .card-front .wordmark { color: var(--white); font-size: 44px; }
  .wordmark .sub { display: block; font-size: 0.62em; letter-spacing: 0.02em; }

  /* Back */
  .card-back {
    left: 605px; top: 500px;
    background: var(--white);
  }
  .card-back .band {
    position: absolute; left: 0; right: 0; bottom: 0; height: 100px;
    background: var(--brand-blue);
  }
  .card-back .accent-circle {
    position: absolute; right: 40px; top: 92px;
    width: 150px; height: 150px; border-radius: 50%;
    background: var(--brand-blue);
    border: 5px solid var(--white);
  }
  .card-back .wordmark {
    position: absolute; left: 34px; top: 30px;
    color: var(--ink); font-size: 24px;
  }
  .holder { position: absolute; left: 34px; top: 100px; }
  .holder-name {
    font-family: "Cinzel", serif; font-weight: 500;
    color: var(--brand-blue); font-size: 19px; letter-spacing: 0.01em;
  }
  .holder-role, .address {
    font-family: "Montserrat", sans-serif; color: var(--ink-soft);
    font-size: 12.5px;
  }
  .holder-role { margin-top: 2px; }
  .address { margin-top: 12px; line-height: 1.35; }

  .contacts {
    position: absolute; left: 34px; bottom: 14px;
    list-style: none;
    font-family: "Montserrat", sans-serif; font-size: 12.5px; color: var(--white);
  }
  .contacts li { display: flex; align-items: center; gap: 8px; line-height: 1.55; }
  .contacts svg { width: 11px; height: 11px; fill: none; stroke: var(--white); stroke-width: 1.6; }
</style>
</head>
<body>
<main class="stage">

  <section class="card card-front">
    <div class="wordmark">KEYSTONE<span class="sub">CHIROPRACTIC</span></div>
  </section>

  <section class="card card-back">
    <div class="band"></div>
    <div class="accent-circle"></div>

    <div class="wordmark">KEYSTONE<span class="sub">CHIROPRACTIC</span></div>

    <div class="holder">
      <p class="holder-name">DANIEL HARTLEY</p>
      <p class="holder-role">Director</p>
      <p class="address">1187 Larkspur Lane<br>Salem, OR 97301</p>
    </div>

    <ul class="contacts">
      <li>
        <svg viewBox="0 0 12 12"><path d="M3 1 L5 3.5 L4 5 Q5.5 7 7 8 L8.5 7 L11 9 L9.5 11 Q4 10 1 2.5 Z"/></svg>
        (555) 214-3690
      </li>
      <li>
        <svg viewBox="0 0 12 12"><rect x="1" y="2.5" width="10" height="7"/><path d="M1 2.5 L6 6.5 L11 2.5"/></svg>
        info@keystonechiro.com
      </li>
      <li>
        <svg viewBox="0 0 12 12"><circle cx="6" cy="6" r="5"/><path d="M1 6 H11 M6 1 Q3 6 6 11 M6 1 Q9 6 6 11"/></svg>
        www.keystonechiro.com
      </li>
    </ul>
  </section>

</main>
</body>
</html>
```